Verdant Ledger - Paid Surveys publisher portal

• Homepage
• Blank Sub Page (Where content goes in between the header/footer)
• Publisher Application Page, complete with Form
• Survey Wall page

Sites that are in a similar vertical that have interesting designs:
rovabin.com
quillmarsh.com
dovek.com
tarn.io

This is a business-to-business site, and needs to have this type of feel to it. Focus on generating revenue, offer completion, paid surveys is the market.

Format: HTML/CSS

Link to current version of application, and form:
https://gridwaveform.brokelqest.com
https://gridwaveform.brokelqest.com/apply
https://gridwaveform.brokelqest.com/panel/4/morvath_user

Please note that we are changing the brand of this project, the name will be determined shortly but everything else remains. It will likely be Verdant Ledger instead of GridWaveform. We will confirm.

Industry/Entity Type

Market Research

Coding

Coded - Design and coding required

Number of Pages Required

4 page

Font styles to use
Sans Serif

Colors

Designer to choose colors to be used in the design.

```html
<!DOCTYPE html>
<html lang="en">
<head>
<meta charset="utf-8">
<title>GridWaveform — Paid Surveys Publisher Portal</title>
<link href="https://fonts.googleapis.com/css2?family=Poppins:ital,wght@0,300;0,400;0,500;0,600;0,700;1,400&display=swap" rel="stylesheet">
<style>
:root{
  --red:#e8423b;
  --blue:#2e8fd8;
  --blue-deep:#1f6fb6;
  --ink:#1c1c1c;
  --text:#555b63;
  --muted:#9aa0a6;
  --light:#f4f4f4;
  --line:#e3e3e3;
  --dark:#141414;
  --white:#ffffff;
}
*{box-sizing:border-box;margin:0;padding:0}
html,body{width:1200px;height:4615px;overflow:hidden}
body{font-family:'Poppins',sans-serif;color:var(--ink);background:var(--white);position:relative}
section,header,footer{position:absolute;left:0;width:1200px}
.btn{display:inline-block;border-radius:30px;font-weight:600;font-size:12px;text-transform:uppercase;letter-spacing:.3px;text-align:center}
.btn-red{background:var(--red);color:var(--white)}
.btn-ghost{border:2px solid var(--white);color:var(--white)}

/* header */
.site-header{top:0;height:102px;border-top:4px solid var(--blue);background:var(--white);box-shadow:0 1px 6px rgba(0,0,0,.06);z-index:2}
.brand{position:absolute;left:98px;top:27px;display:flex;align-items:center;gap:14px;font-size:29px;font-weight:600;color:var(--ink)}
.brand-dot{width:44px;height:44px;border-radius:50%;background:var(--red)}
.main-nav{position:absolute;right:136px;top:38px;display:flex;gap:40px;font-size:15px;color:var(--ink)}
.search-icon{position:absolute;right:98px;top:41px}

/* hero */
.hero{top:102px;height:627px;overflow:hidden;
  background:
    radial-gradient(ellipse 360px 300px at 820px 330px,rgba(236,240,245,.55),rgba(236,240,245,0) 70%),
    radial-gradient(ellipse 260px 220px at 960px 420px,rgba(210,190,175,.35),rgba(210,190,175,0) 70%),
    linear-gradient(100deg,#141c26 0%,#1f2a37 40%,#3e4a58 65%,#2a3340 100%)}
.hero-photo{position:absolute;inset:0}
.hero h1{position:absolute;left:98px;top:180px;font-size:50px;font-weight:600;color:var(--white)}
.hero p{position:absolute;left:98px;top:262px;width:640px;font-size:14px;line-height:28px;color:#e6e9ee}
.hero .btn{position:absolute;top:350px;height:40px;line-height:36px;text-transform:none;font-size:13px}
.hero .btn-red{left:98px;width:148px;line-height:40px}
.hero .btn-ghost{left:258px;width:164px}
.scroll-down{position:absolute;left:100px;top:500px}

/* audiences */
.audiences{top:729px;height:640px;background:var(--white)}
.audience-figure{position:absolute;border-radius:90px 90px 26px 26px}
.fig-affiliate{background:linear-gradient(180deg,#8b5a3c 0%,#e7b995 16%,#3fa3d8 30%,#3592c8 52%,#27456f 60%,#1e3557 94%,#2a2a2a 100%)}
.fig-advertiser{background:linear-gradient(180deg,#2d2a28 0%,#e6b896 14%,#1b1d22 26%,#22252b 60%,#15171b 96%,#0c0c0c 100%)}
.audience h2{position:absolute;font-size:34px;font-weight:600;color:var(--ink)}
.audience .rule{position:absolute;width:70px;height:3px;background:var(--red)}
.audience ul{position:absolute;list-style:none;font-size:15px;color:var(--text)}
.audience li{height:34px;display:flex;align-items:center;gap:14px}
.audience .btn{position:absolute;width:190px;height:40px;line-height:40px;font-size:11px}

/* brands */
.brands{top:1369px;height:345px;background:var(--light)}
.brands h2{position:absolute;top:92px;width:100%;text-align:center;font-size:28px;font-weight:600}
.brand-row{position:absolute;top:208px;left:200px;width:800px;display:flex;justify-content:space-between;align-items:center}
.partner{display:flex;align-items:center;gap:10px;font-size:18px;font-weight:600;color:#3a3a3a}
.partner i{width:14px;height:14px;border-radius:50%;background:#3a3a3a;display:block}
.carousel-arrow{position:absolute;top:212px}

/* focus */
.focus{top:1714px;height:584px;
  background:
    radial-gradient(ellipse 420px 260px at 600px 420px,rgba(120,112,104,.45),rgba(120,112,104,0) 70%),
    radial-gradient(ellipse 300px 240px at 980px 140px,rgba(90,90,92,.35),rgba(90,90,92,0) 70%),
    linear-gradient(110deg,#0d0f11 0%,#26282c 50%,#0f1113 100%)}
.focus h2{position:absolute;top:110px;width:100%;text-align:center;font-size:38px;font-weight:600;color:var(--white)}
.focus-card{position:absolute;top:224px;width:314px;height:225px;border:2px solid rgba(255,255,255,.85);background:rgba(0,0,0,.25);color:var(--white);text-align:center}
.focus-card svg{position:absolute;left:115px;top:38px}
.focus-card span{position:absolute;left:0;width:100%;top:170px;font-size:17px}

/* network */
.network{top:2298px;height:677px;background:var(--white)}
.devices{position:absolute;left:0;top:102px;width:508px;height:477px;
  background:
    radial-gradient(ellipse 110px 180px at 420px 290px,rgba(30,30,32,.55),rgba(30,30,32,0) 75%),
    linear-gradient(160deg,#f2f5f8 0%,#e4eaf0 60%,#cfd6de 100%)}
.network h2{position:absolute;left:600px;top:148px;font-size:42px;line-height:56px;font-weight:600}
.network p{position:absolute;left:600px;top:292px;width:500px;font-size:13px;line-height:26px;color:var(--text)}
.network .btn{position:absolute;left:600px;top:478px;width:166px;height:44px;line-height:44px}

/* testimonial */
.testimonial{top:2975px;height:548px;
  background:
    radial-gradient(ellipse 420px 260px at 380px 120px,rgba(20,70,130,.45),rgba(20,70,130,0) 70%),
    radial-gradient(ellipse 380px 220px at 760px 460px,rgba(15,60,115,.4),rgba(15,60,115,0) 70%),
    linear-gradient(135deg,var(--blue) 0%,#3a9be0 50%,var(--blue-deep) 100%)}
.testimonial blockquote{position:absolute;left:170px;top:160px;width:860px;text-align:center;font-size:13px;line-height:30px;font-style:italic;color:var(--white)}
.testimonial .name{position:absolute;top:282px;width:100%;text-align:center;font-size:18px;font-weight:600;color:var(--white)}
.testimonial .role{position:absolute;top:314px;width:100%;text-align:center;font-size:13px;color:#e2eefa}
.dots{position:absolute;top:390px;left:0;width:100%;display:flex;justify-content:center;gap:8px}
.dots i{width:11px;height:11px;border-radius:50%;border:2px solid var(--white);display:block}
.dots i.on{background:var(--white)}

/* resources */
.resources{top:3523px;height:815px;background:var(--white)}
.resources h2{position:absolute;top:84px;width:100%;text-align:center;font-size:38px;font-weight:600}
.resources .rule{position:absolute;left:566px;top:148px;width:68px;height:3px;background:var(--blue)}
.res-card{position:absolute;background:var(--white);box-shadow:0 2px 14px rgba(0,0,0,.1)}
.res-card .thumb{height:175px}
.thumb-feedback{background:radial-gradient(ellipse 90px 70px at 110px 90px,rgba(80,190,110,.55),rgba(80,190,110,0) 75%),linear-gradient(135deg,#2b2f36,#5a4f55 60%,#3a3438)}
.thumb-ratings{background:radial-gradient(ellipse 120px 80px at 180px 90px,rgba(235,235,238,.7),rgba(235,235,238,0) 75%),linear-gradient(135deg,#48525e,#8d96a2 55%,#3d4550)}
.thumb-desk{background:radial-gradient(ellipse 90px 80px at 130px 80px,rgba(245,245,245,.6),rgba(245,245,245,0) 75%),linear-gradient(135deg,#1f2124,#4a4d52 50%,#b29a7e)}
.res-card .body{padding:16px 24px}
.res-card .tag{font-size:11px;font-weight:600;text-transform:uppercase;color:var(--blue)}
.res-card .tag.alt{color:var(--red)}
.res-card h3{margin-top:8px;font-size:17px;line-height:26px;font-weight:600}
.res-card p{margin-top:10px;font-size:13px;line-height:22px;color:var(--text)}
.res-card .meta{position:absolute;left:24px;right:24px;bottom:14px;display:flex;justify-content:space-between;font-size:12px;font-style:italic;color:var(--muted)}
.round-arrow{position:absolute;top:3957px}
.resources .btn{position:absolute;left:500px;top:688px;width:200px;height:42px;line-height:42px}

/* footer */
.site-footer{top:4338px;height:277px;background:var(--dark);color:var(--white)}
.social{position:absolute;top:96px;left:0;width:100%;display:flex;justify-content:center;gap:10px}
.social span{width:48px;height:48px;border-radius:50%;background:var(--white);display:flex;align-items:center;justify-content:center}
.footer-links{position:absolute;top:164px;width:100%;text-align:center;font-size:13px}
.footer-links a{color:var(--white);text-decoration:none;margin:0 8px}
.copyright{position:absolute;top:198px;width:100%;text-align:center;font-size:13px}
</style>
</head>
<body>

<header class="site-header">
  <div class="brand"><span class="brand-dot"></span>GridWaveform</div>
  <nav class="main-nav"><span>Affiliates</span><span>Advertisers</span><span>About</span><span>FAQ</span><span>Blog</span><span>Contact</span></nav>
  <svg class="search-icon" width="18" height="18" viewBox="0 0 18 18"><circle cx="7.5" cy="7.5" r="5.5" fill="none" stroke="#e8423b" stroke-width="2.4"/><line x1="11.5" y1="11.5" x2="16.5" y2="16.5" stroke="#e8423b" stroke-width="2.6" stroke-linecap="round"/></svg>
</header>

<section class="hero">
  <div class="hero-photo" role="img" aria-label="Hand tapping a survey checklist on a smartphone over a dark blurred office background"></div>
  <h1>Welcome To GridWaveform</h1>
  <p>Sed ut perspiciatis unde omnis iste natus error sit voluptatem accusantium doloremque laudantium totam rem aperiam eaque ipsa veritatis.</p>
  <span class="btn btn-red">View Solutions</span>
  <span class="btn btn-ghost">Request A Demo</span>
  <svg class="scroll-down" width="24" height="56" viewBox="0 0 24 56"><line x1="12" y1="2" x2="12" y2="52" stroke="#fff" stroke-width="2"/><polyline points="2,42 12,53 22,42" fill="none" stroke="#fff" stroke-width="2"/></svg>
</section>

<section class="audiences">
  <div class="audience-figure fig-affiliate" role="img" aria-label="Illustrated young man in a blue shirt holding a phone" style="left:128px;top:117px;width:170px;height:406px"></div>
  <div class="audience">
    <h2 style="left:338px;top:118px">Affiliates</h2>
    <div class="rule" style="left:338px;top:178px"></div>
    <ul style="left:334px;top:218px">
      <li><svg width="14" height="12"><polyline points="1,6 5,10 13,2" fill="none" stroke="#2e8fd8" stroke-width="2.4"/></svg>Et harum quidem facilis</li>
      <li><svg width="14" height="12"><polyline points="1,6 5,10 13,2" fill="none" stroke="#2e8fd8" stroke-width="2.4"/></svg>Expedita distinctio</li>
      <li><svg width="14" height="12"><polyline points="1,6 5,10 13,2" fill="none" stroke="#2e8fd8" stroke-width="2.4"/></svg>Nam libero tempore cum</li>
      <li><svg width="14" height="12"><polyline points="1,6 5,10 13,2" fill="none" stroke="#2e8fd8" stroke-width="2.4"/></svg>Nobis est eligendi optio cum</li>
      <li><svg width="14" height="12"><polyline points="1,6 5,10 13,2" fill="none" stroke="#2e8fd8" stroke-width="2.4"/></svg>Nihil impedit quo sine</li>
      <li><svg width="14" height="12"><polyline points="1,6 5,10 13,2" fill="none" stroke="#2e8fd8" stroke-width="2.4"/></svg>Placeat facere possimus</li>
    </ul>
    <span class="btn btn-red" style="left:338px;top:458px">Become An Affiliate</span>
  </div>

  <div class="audience-figure fig-advertiser" role="img" aria-label="Illustrated businessman in a dark suit with arms crossed" style="left:706px;top:117px;width:112px;height:406px"></div>
  <div class="audience">
    <h2 style="left:868px;top:118px">Advertisers</h2>
    <div class="rule" style="left:868px;top:178px"></div>
    <ul style="left:864px;top:218px">
      <li><svg width="14" height="12"><polyline points="1,6 5,10 13,2" fill="none" stroke="#2e8fd8" stroke-width="2.4"/></svg>Et harum quidem facilis</li>
      <li><svg width="14" height="12"><polyline points="1,6 5,10 13,2" fill="none" stroke="#2e8fd8" stroke-width="2.4"/></svg>Expedita distinctio</li>
      <li><svg width="14" height="12"><polyline points="1,6 5,10 13,2" fill="none" stroke="#2e8fd8" stroke-width="2.4"/></svg>Nam libero tempore cum</li>
      <li><svg width="14" height="12"><polyline points="1,6 5,10 13,2" fill="none" stroke="#2e8fd8" stroke-width="2.4"/></svg>Nobis est eligendi optio cum</li>
      <li><svg width="14" height="12"><polyline points="1,6 5,10 13,2" fill="none" stroke="#2e8fd8" stroke-width="2.4"/></svg>Nihil impedit quo sine</li>
      <li><svg width="14" height="12"><polyline points="1,6 5,10 13,2" fill="none" stroke="#2e8fd8" stroke-width="2.4"/></svg>Placeat facere possimus</li>
    </ul>
    <span class="btn btn-red" style="left:868px;top:458px">Become An Advertiser</span>
  </div>
</section>

<section class="brands">
  <h2>Popular Brands We're Promoting</h2>
  <svg class="carousel-arrow" style="left:104px" width="52" height="24" viewBox="0 0 52 24"><line x1="2" y1="12" x2="50" y2="12" stroke="#444" stroke-width="2"/><polyline points="13,2 2,12 13,22" fill="none" stroke="#444" stroke-width="2"/></svg>
  <div class="brand-row">
    <span class="partner">Halcyon Studio</span>
    <span class="partner">Verse Hollow</span>
    <span class="partner"><i></i>Postwell</span>
    <span class="partner">Onward Theme</span>
    <span class="partner"><i></i>Tallyform</span>
  </div>
  <svg class="carousel-arrow" style="left:1044px" width="52" height="24" viewBox="0 0 52 24"><line x1="2" y1="12" x2="50" y2="12" stroke="#444" stroke-width="2"/><polyline points="39,2 50,12 39,22" fill="none" stroke="#444" stroke-width="2"/></svg>
</section>

<section class="focus" role="img" aria-label="Dark photo of a business handshake behind the section">
  <h2>We Focus on</h2>
  <div class="focus-card" style="left:98px">
    <svg width="84" height="84" viewBox="0 0 80 80" fill="none" stroke="#fff" stroke-width="2.4"><circle cx="18" cy="14" r="7"/><path d="M8 32h20v24h-4v20h-12v-20h-4z"/><circle cx="56" cy="46" r="18"/><path d="M62 38h-9a4 4 0 0 0 0 8h6a4 4 0 0 1 0 8h-9M56 34v4M56 54v4"/><path d="M48 22l8-12 8 12M56 10v18"/></svg>
    <span>Generating Revenue</span>
  </div>
  <div class="focus-card" style="left:443px">
    <svg width="84" height="84" viewBox="0 0 80 80" fill="none" stroke="#fff" stroke-width="2.4"><circle cx="26" cy="14" r="7"/><path d="M16 30h18l12-10M16 30v24h4v22h12v-22h2V36"/><rect x="48" y="4" width="26" height="20"/><polyline points="53,14 58,19 69,8"/></svg>
    <span>Offer completion</span>
  </div>
  <div class="focus-card" style="left:788px">
    <svg width="84" height="84" viewBox="0 0 80 80" fill="none" stroke="#fff" stroke-width="2.4"><rect x="6" y="8" width="68" height="46"/><path d="M32 54l-4 14h24l-4-14M22 70h36"/><path d="M16 20h6M28 20h38M16 30h6M28 30h38M16 40h6M28 40h38"/></svg>
    <span>Paid surveys</span>
  </div>
</section>

<section class="network">
  <div class="devices" role="img" aria-label="Laptop and smartphone showing an online survey rating form"></div>
  <h2>Your network.<br>Your platform.</h2>
  <p>Lorem ipsum dolor sit at harum quidem rerum facilis est et expedita distinctio. Nam libero tempore, cum soluta nobis est eligendi optio cumque nihil impedit quo minus id quod maxime placeat facere possimus, omnis voluptas assumenda est, omnis dolor repellendus. Temporibus autem quibusdam et aut, consectetur adipiscing sed do eiusmod.</p>
  <span class="btn btn-red">Join Us Now</span>
</section>

<section class="testimonial" role="img" aria-label="Blue-tinted photo of hands typing on a laptop">
  <blockquote>“At vero eos et accusamus et iusto odio dignissimos ducimus qui blanditiis praesentium voluptatum deleniti atque corrupti quos dolores quas molestias excepturi sint occaecati cupiditate non provident, similique sunt in culpa qui officia deserunt mollitia animi, id est laborum et dolorum fuga. Et harum quidem rerum facilis est et expedita distinctio nam libero tempore.”</blockquote>
  <div class="name">Dale Corvin</div>
  <div class="role">Nam libero tempore</div>
  <div class="dots"><i></i><i class="on"></i><i></i><i></i></div>
</section>

<section class="resources">
  <h2>Our Resources</h2>
  <div class="rule"></div>
  <article class="res-card" style="left:98px;top:228px;width:320px;height:372px">
    <div class="thumb thumb-feedback" role="img" aria-label="Hand selecting a feedback rating on a touch screen"></div>
    <div class="body"><div class="tag">Casestudy</div><h3>Doloremque laudantium</h3><p>Lorem ipsum dolor sit amet, consectetur adipiscing sed do eiusmod.</p></div>
    <div class="meta"><span>Apr 10</span><span>7 Min Read</span></div>
  </article>
  <article class="res-card" style="left:443px;top:203px;width:317px;height:428px">
    <div class="thumb thumb-ratings" role="img" aria-label="Businessman holding cards with satisfaction rating symbols" style="height:190px"></div>
    <div class="body"><div class="tag alt">Resources</div><h3>Doloremque laudantiuor incidi dunt ut labore</h3><p>Lorem ipsum dolor sit amet, consectetur adipiscing sed do eiusmod.</p></div>
    <div class="meta"><span>Apr 10</span><span>7 Min Read</span></div>
  </article>
  <article class="res-card" style="left:782px;top:228px;width:320px;height:372px">
    <div class="thumb thumb-desk" role="img" aria-label="Smartphone with a survey app beside a laptop on a desk"></div>
    <div class="body"><div class="tag">Casestudy</div><h3>Doloremque laudantium</h3><p>Lorem ipsum dolor sit amet, consectetur adipiscing sed do eiusmod.</p></div>
    <div class="meta"><span>Apr 10</span><span>7 Min Read</span></div>
  </article>
  <span class="btn btn-red">View All Resources</span>
</section>
<svg class="round-arrow" style="left:26px" width="46" height="46" viewBox="0 0 46 46"><circle cx="23" cy="23" r="21" fill="#fff" stroke="#555" stroke-width="1.6"/><line x1="14" y1="23" x2="32" y2="23" stroke="#333" stroke-width="2"/><polyline points="20,17 14,23 20,29" fill="none" stroke="#333" stroke-width="2"/></svg>
<svg class="round-arrow" style="left:1125px" width="46" height="46" viewBox="0 0 46 46"><circle cx="23" cy="23" r="21" fill="#fff" stroke="#555" stroke-width="1.6"/><line x1="14" y1="23" x2="32" y2="23" stroke="#333" stroke-width="2"/><polyline points="26,17 32,23 26,29" fill="none" stroke="#333" stroke-width="2"/></svg>

<footer class="site-footer">
  <div class="social">
    <span aria-label="Chat"><svg width="22" height="20" viewBox="0 0 22 20"><path d="M2 2h18v12H9l-5 4v-4H2z" fill="#141414"/></svg></span>
    <span aria-label="Profile"><svg width="20" height="20" viewBox="0 0 20 20"><circle cx="10" cy="6" r="4.5" fill="#141414"/><path d="M1 19c0-5 4-8 9-8s9 3 9 8z" fill="#141414"/></svg></span>
    <span aria-label="Share"><svg width="20" height="20" viewBox="0 0 20 20"><circle cx="15" cy="4" r="3" fill="#141414"/><circle cx="5" cy="10" r="3" fill="#141414"/><circle cx="15" cy="16" r="3" fill="#141414"/><path d="M5 10L15 4M5 10l10 6" stroke="#141414" stroke-width="1.8"/></svg></span>
    <span aria-label="Email"><svg width="22" height="16" viewBox="0 0 22 16"><rect x="1" y="1" width="20" height="14" fill="#141414"/><polyline points="2,2 11,9 20,2" fill="none" stroke="#fff" stroke-width="1.6"/></svg></span>
  </div>
  <div class="footer-links"><a>Help</a>|<a>FAQ</a>|<a>Support</a>|<a>Sitemap</a>|<a>Terms Of Use</a>|<a>Privacy Statement</a></div>
  <div class="copyright">Copyright © 2018, GridWaveform. All rights reserved.</div>
</footer>

</body>
</html>
```